Business Card Design

We are a residential half way house for the addict ,the alcoholic and dual diagnosed in recovery.
i house both men and woman age 18+

Industry/Entity Type

Residential

```html
<!DOCTYPE html>
<html lang="en">
<head>
<meta charset="utf-8">
<title>Cedar Path Recovery Home – Business Card</title>
<link rel="stylesheet" href="https://fonts.googleapis.com/css2?family=Tinos:wght@400&display=swap">
<style>
  :root {
    --backdrop: #e9e7e3;
    --card-white: #ffffff;
    --slate: #626b7e;
    --slate-dark: #586173;
    --ink: #1b1b1d;
    --on-slate: #f3f4f7;
    --divider: #e6e8ee;
  }
  * { box-sizing: border-box; margin: 0; padding: 0; }
  html, body {
    width: 1200px; height: 892px; overflow: hidden;
    background: var(--backdrop);
  }
  .canvas {
    position: relative; width: 1200px; height: 892px;
    display: flex; align-items: center; justify-content: center;
  }
  .card {
    position: relative; width: 1000px; height: 572px;
    border-radius: 34px; overflow: hidden;
    background: linear-gradient(180deg, var(--slate) 0%, var(--slate-dark) 100%);
    box-shadow: 0 18px 40px rgba(0,0,0,0.18);
  }
  .card__header {
    position: absolute; left: 0; top: 0; width: 100%; height: 172px;
    background: var(--card-white);
  }
  .brand {
    position: absolute; right: 70px; top: 34px; text-align: right;
    font-family: "Tinos", "Times New Roman", serif; color: var(--ink);
    font-weight: 400; font-size: 46px; line-height: 1.12;
  }
  .holder {
    position: absolute; right: 470px; top: 226px; text-align: right;
    font-family: "Tinos", "Times New Roman", serif; color: var(--on-slate);
  }
  .holder__name { font-size: 44px; line-height: 1.05; }
  .holder__role, .holder__note { font-size: 25px; line-height: 1.15; }
  .holder__address { font-size: 26px; line-height: 1.2; margin-top: 4px; }
  .divider {
    position: absolute; left: 560px; top: 220px; width: 2px; height: 260px;
    background: var(--divider);
  }
  .contact {
    position: absolute; left: 590px; top: 270px; list-style: none;
    font-family: "Tinos", "Times New Roman", serif; color: var(--on-slate);
    font-size: 27px; line-height: 1.3;
  }
  .contact__item { display: flex; align-items: center; gap: 12px; }
  .contact__icon { width: 26px; height: 22px; flex: none; fill: var(--on-slate); }
</style>
</head>
<body>
<main class="canvas">
  <article class="card">
    <header class="card__header">
      <div class="brand">Cedar Path<br>Recovery Home</div>
    </header>

    <section class="holder">
      <div class="holder__name">Dana Whitfield</div>
      <div class="holder__role">Owner</div>
      <div class="holder__note">(15 yrs.in recovery)</div>
      <div class="holder__address">2718 Palm Grove Rd. Lake Haven,<br>Fla 33400</div>
    </section>

    <div class="divider"></div>

    <ul class="contact">
      <li class="contact__item">
        <svg class="contact__icon" viewBox="0 0 26 22" aria-hidden="true"><path d="M2 7c0-3 5-5 11-5s11 2 11 5v2h-5V7c-2-1-4-1-6-1s-4 0-6 1v2H2z"/><path d="M6 10h14l3 10H3z"/></svg>
        <span>(555) 237-8140</span>
      </li>
      <li class="contact__item">
        <svg class="contact__icon" viewBox="0 0 26 22" aria-hidden="true"><path d="M2 7c0-3 5-5 11-5s11 2 11 5v2h-5V7c-2-1-4-1-6-1s-4 0-6 1v2H2z"/><path d="M6 10h14l3 10H3z"/></svg>
        <span>(555) 237-8141</span>
      </li>
      <li class="contact__item">
        <svg class="contact__icon" viewBox="0 0 26 22" aria-hidden="true"><rect x="7" y="1" width="12" height="6"/><rect x="2" y="8" width="22" height="9" rx="2"/><rect x="7" y="15" width="12" height="6"/></svg>
        <span>(555) 392-6074</span>
      </li>
      <li class="contact__item">
        <svg class="contact__icon" viewBox="0 0 26 22" aria-hidden="true"><path d="M2 4h22v14H2z" fill="none" stroke="#f3f4f7" stroke-width="2"/><path d="M2 4l11 9 11-9" fill="none" stroke="#f3f4f7" stroke-width="2"/></svg>
        <span>d.whitfield@example.com</span>
      </li>
    </ul>
  </article>
</main>
</body>
</html>
```